QUORVIN CAPABILITY STATEMENT “Shaping Lasting Links”

QUORVIN CAPABILITY STATEMENT
“Shaping Lasting Links”
Indigenous-Owned Telecommunications & Infrastructure Solutions Partner

COVER PAGE

Visual: Modern and clean design featuring telecom towers, wind turbines, civil infrastructure, roads, and community WiFi imagery.
Tagline: “Linking Places, Lifting Futures.”
Contact:
Website: www.quorvin.com.au
Email: info@quorvin.com.au
Phone: [Insert Main Number]
“Proudly Indigenous-Owned | Compliant with Aboriginal Procurement Policy (APP) & SME Policies”
INTRODUCTION

Quorvin is a 100% Indigenous-owned leader in comprehensive infrastructure solutions, specializing in telecommunications, civil works, renewable energy, structural engineering, and site development. With over a decade of experience, we deliver safe, reliable, and culturally respectful services across Australia, from urban centers to remote wind farms and heritage sites. Our mission: “To bridge infrastructure gaps while empowering Indigenous communities and fostering sustainable growth.”

CORE CAPABILITIES

TELECOMMUNICATIONS

Tower Builds & Maintenance: Structural engineering, geotechnical analysis, foundation mapping.
Community WiFi Projects: Enhancing digital inclusion in Indigenous and remote communities.
Fiber & Wireless Networks: End-to-end installation for Velonet, Satellite, and regional connectivity.
Height Safety Systems: Design, inspection, and certification of lad-safe safety infrastructure.
CIVIL & STRUCTURAL ENGINEERING

Foundations & Concreting: Reinforced slabs, grillage, geotech-to-construction turnkey solutions.
Site Development: Earthworks, drainage, and access road/track construction.
Wind Farm Infrastructure: Reinforcing towers and integrating power systems for high-wind environments.
ROAD & ACCESS TRACK CONSTRUCTION

Construction of durable access roads and tracks: For remote projects and urban settings.
Remediation of existing tracks: Upgrading for environmental compliance and sustainability.
Facilitating logistics and site access: Particularly in challenging terrain.
POWER & ELECTRICAL SYSTEMS

Off-grid energy solutions: Solar hybrid systems, electrical structural engineering.
Grid upgrades: Ensuring compliance with AS/NZS standards and facilitating connection upgrades.
SITE REFURBISHMENT & DEMOLITION

Comprehensive refurbishment and demolition services: For outdated telecom sites and structures.
Environmentally responsible dismantling: Focused on recycling materials and minimizing land impact.
EMERGENCY RESPONSE SERVICES

24/7 Rapid Response: Over 450 callouts annually; 4,000+ emergencies resolved nationwide.
Disaster Recovery: Comprehensive support during floods, bushfires for Velonet, Marvaske, Trilumen, and regional clients.
PROJECT EXPERIENCE

Heritage Tower Upgrade

Enhanced safety and technology on culturally significant heritage sites, preserving their integrity.
Wind Farm Deployment

Delivered power, fiber, and reinforced foundations for large-scale renewable energy projects in high-wind environments.
Regional Fibre Network

Laid 200km of fiber in flood-prone regions, ensuring critical infrastructure resilience.
Indigenous Community WiFi & Connectivity

Installed sustainable WiFi networks to bridge the digital divide, supporting education, health, and business activities.
Site Demolition & Refurbishment

Safely decommissioned aging telecom sites and structures across Australia, emphasizing land reuse and environmental care.
Access Track Construction & Remediation

Developed new access roads and refurbished existing tracks to facilitate project logistics, particularly in remote or environmentally sensitive areas.
Key Stats:
+600 sites supported | 10-year Velonet partner | 98% client retention | Over 20 Indigenous community WiFi deployments

COMMITMENT TO SAFETY & QUALITY

“Pause Twice, Work Wise” Protocol: Enforced pre-task risk assessments to ensure safety at every stage.
Certifications: ISO 45001 (Safety) | ISO 9001 (Quality Management).
Safety Culture: Regular safety audits, Indigenous-led training programs, and safety initiatives focused on community well-being.
INDIGENOUS INCLUSION & COMMUNITY IMPACT

Elders Guidance Council: Provides guidance on community engagement, cultural sensitivity, and social responsibility.
Supplier Diversity: 30% procurement from Indigenous-owned businesses, fostering economic growth.
Regional Employment: 65% of our workforce originates from local communities, creating sustainable jobs.
Testimonial: “Quorvin’s partnership empowered our community with jobs and infrastructure that respects our land.” – Local Indigenous Leader

CONTACT & SERVICE AREAS

Headquarters: [Insert Address] | ABN: [Insert ABN]

24/7 Emergency Support: [Insert Dedicated Emergency Line]

Certifications & Registrations:

Trade Circle Registered, First Enterprise Register (FER)
SERVICE AREAS

National Coverage with Regional Expertise:
Major Cities: Sydney, Melbourne, Brisbane, Perth, Adelaide, Darwin, Hobart.
Regional & Remote Areas: Pilbara, Kimberley, Far North Queensland, Outback NSW.
Disaster Zones: Rapid response teams deployed nationwide for bushfire and flood incidents.
EMERGENCY SUPPORT

SLA Guarantee: 90% of emergencies addressed within 4 hours.
Partners Supported: Velonet, Marvaske, Trilumen, regional councils.
This capability statement reflects our commitment to quality, safety, and community engagement across all levels of operation, ensuring that we empower the communities we serve while maintaining the highest standards of service delivery.

Target Market(s)

Government Agencies: Especially those seeking to comply with Indigenous Procurement Policies. Telecommunication Operators: Such as Velonet, Marvaske, and Trilumen for infrastructure deployment. Indigenous Communities: Projects aimed at enhancing connectivity and digital inclusion. Utilities and Energy Providers: For power and electrical infrastructure projects. Construction and Engineering Firms: Seeking collaboration on civil and structural infrastructure projects.

Industry/Entity Type

Telecommunications and Infrastructure Development: Focused on service delivery in various contexts, including urban settings, remote locations, and Indigenous community projects. Renewable Energy: This includes wind and solar infrastructure linked to telecommunications enhancements. Civil Engineering: Related to building and maintaining essential infrastructure such as access roads and utility lines.

Font styles to use
Other font styles liked:
• Bubbleboddy neue

Requirements
Must have
• Clear demonstration of Indigenous ownership and community engagement. Compliance with relevant safety and quality certifications (e.g., ISO 45001, ISO 9001). Showcase of core capabilities in telecommunications, civil engineering, and those specific to renewable energy. Visuals that reflect the diverse range of services offered (like telecom towers and community WiFi installations).
Nice to have
• Interactive elements such as hyperlinks to project case studies or client testimonials. Infographics or visual data to highlight key statistics and project success rates. Cultural motifs or imagery that reflect Indigenous heritage and inclusion in design aspirations. QR codes that link to videos or more detailed project descriptions for digital formats.
Should not have
• Clutter or excessive text that detracts from the main messages. Generic stock images that don’t align with the specific projects or Indigenous culture. Technical jargon that could confuse stakeholders unfamiliar with industry-specific terms. Overemphasis on competitors; the focus should remain on Quorvin's unique strengths and contributions.

```html
<!DOCTYPE html>
<html lang="en">
<head>
<meta charset="utf-8">
<title>Quorvin Capability Statement – Pages 4–5</title>
<link href="https://fonts.googleapis.com/css2?family=Montserrat:wght@300;400;500;600;700;800&display=swap" rel="stylesheet">
<style>
:root{
  --red:#e4262b;
  --red-deep:#c8161d;
  --pink:#f26262;
  --rule-pink:#f0b4b4;
  --ink:#1c1c1c;
  --text:#2a2a2a;
  --grey-head:#565656;
  --panel:#f3f3f3;
  --stage:#dcdcdc;
  --paper:#ffffff;
}
*{margin:0;padding:0;box-sizing:border-box}
html,body{width:1200px;height:842px;overflow:hidden;background:var(--stage)}
body{font-family:'Montserrat',sans-serif;color:var(--text)}
.stage{position:absolute;left:0;top:0;width:2296px;height:1611px;transform:scale(0.52265);transform-origin:0 0;background:var(--stage)}
.paper{position:absolute;left:85px;top:117px;width:2126px;height:1377px;background:var(--paper)}
.shapes{position:absolute;left:0;top:0;width:2296px;height:1611px}

.section-title{position:absolute;left:166px;font-size:26px;font-weight:700;letter-spacing:.2px}
.section-title.red{color:var(--red-deep)}
.section-title.dark{color:var(--ink)}
.section-title.grey{color:var(--grey-head)}

.row{position:absolute;left:166px;width:905px;height:58px;background:var(--panel);display:flex;align-items:center}
.row-label{height:100%;display:flex;align-items:center;padding-left:14px;color:#fff;font-size:18px;font-weight:600;line-height:23px;flex-shrink:0;white-space:nowrap;
  clip-path:polygon(0 0,calc(100% - 18px) 0,100% 50%,calc(100% - 18px) 100%,0 100%)}
.row-text{padding-left:14px;font-size:18.5px;letter-spacing:-.2px;line-height:23px;color:var(--text);white-space:nowrap}
.label-red{background:linear-gradient(90deg,var(--red) 0%,#f04848 100%)}
.label-black{background:var(--ink)}
.g1{background:#adadad}.g2{background:#a3a3a3}.g3{background:#999}.g4{background:#8d8d8d}.g5{background:#7c7c7c}.g6{background:#6d6c6c}

.page-footer{position:absolute;top:1401px;width:905px;height:25px;display:flex;align-items:center}
.footer-brand{font-size:18px;font-weight:600;color:var(--ink);letter-spacing:.5px;margin-right:12px;white-space:nowrap}
.rule-dark{width:65px;height:4px;background:#111}
.rule-light{flex:1;height:1.5px;background:var(--rule-pink)}
.page-num{width:25px;height:25px;background:var(--red);color:#fff;font-size:16px;font-weight:700;display:flex;align-items:center;justify-content:center}

.stats-title{position:absolute;left:1251px;top:193px;font-size:32px;line-height:33px;color:var(--ink)}
.stats-title .light{font-weight:400}
.stats-title .bold{font-weight:800;display:block}
.stat-label{position:absolute;width:260px;text-align:center;font-size:19px;letter-spacing:-.2px;line-height:23px;color:var(--text);white-space:nowrap}

.banner-text{position:absolute;left:1230px;top:632px;width:420px;text-align:center;color:#fff}
.banner-text .thin{display:block;font-size:34px;font-weight:400;line-height:38px}
.banner-text .strong{display:block;font-size:35px;font-weight:800;line-height:40px}

.hex-text{position:absolute;color:#fff;text-align:center;font-weight:600;font-size:18px;line-height:22px;display:flex;align-items:center;justify-content:center}
.panel-text{position:absolute;font-size:19px;letter-spacing:-.2px;line-height:23px;color:var(--text);white-space:nowrap}

.impact-head{position:absolute;font-size:19px;font-weight:700;color:var(--ink);white-space:nowrap}
.impact-head.red{color:var(--red)}
.impact-body{position:absolute;font-size:19px;letter-spacing:-.2px;line-height:23px;color:var(--text);white-space:nowrap}
.impact-core{position:absolute;left:1589px;top:1150px;width:180px;text-align:center;font-size:18px;line-height:23px;font-weight:700;color:var(--ink)}
</style>
</head>
<body>
<div class="stage">
  <div class="paper"></div>

  <svg class="shapes" viewBox="0 0 2296 1611" aria-hidden="true">
    <!-- key stats -->
    <rect x="1226" y="197" width="7" height="57" fill="var(--red)"/>
    <g stroke="#9a9a9a" stroke-width="1.5">
      <line x1="1356" y1="385" x2="1471" y2="422"/>
      <line x1="1601" y1="422" x2="1715" y2="385"/>
      <line x1="1846" y1="385" x2="1973" y2="440"/>
    </g>
    <g stroke-width="1.5">
      <line x1="1291" y1="438" x2="1291" y2="466" stroke="var(--red)"/>
      <line x1="1780" y1="438" x2="1780" y2="466" stroke="var(--red)"/>
      <line x1="1536" y1="338" x2="1536" y2="365" stroke="#111"/>
      <line x1="2038" y1="370" x2="2038" y2="397" stroke="#111"/>
    </g>
    <circle cx="1291" cy="466" r="4" fill="var(--red)"/>
    <circle cx="1780" cy="466" r="4" fill="var(--red)"/>
    <circle cx="1536" cy="338" r="4" fill="#111"/>
    <circle cx="2038" cy="370" r="4" fill="#111"/>

    <polygon points="1291,292 1353,327 1353,399 1291,434 1229,399 1229,327" fill="#fff" stroke="var(--red)" stroke-width="9"/>
    <polygon points="1536,369 1598,404 1598,476 1536,511 1474,476 1474,404" fill="#fff" stroke="#111" stroke-width="9"/>
    <polygon points="1780,292 1842,327 1842,399 1780,434 1718,399 1718,327" fill="#fff" stroke="var(--red)" stroke-width="9"/>
    <polygon points="2038,401 2100,436 2100,508 2038,543 1976,508 1976,436" fill="#fff" stroke="#111" stroke-width="9"/>

    <!-- building icon -->
    <g fill="none" stroke="var(--red)" stroke-width="3">
      <rect x="1270" y="328" width="30" height="70"/>
      <rect x="1290" y="355" width="26" height="43"/>
      <line x1="1256" y1="398" x2="1328" y2="398"/>
      <rect x="1276" y="336" width="7" height="7"/><rect x="1287" y="336" width="7" height="7"/>
      <rect x="1276" y="348" width="7" height="7"/><rect x="1276" y="360" width="7" height="7"/>
      <rect x="1276" y="372" width="7" height="7"/>
      <rect x="1296" y="362" width="6" height="6"/><rect x="1306" y="362" width="6" height="6"/>
      <rect x="1296" y="373" width="6" height="6"/><rect x="1306" y="373" width="6" height="6"/>
      <rect x="1296" y="384" width="6" height="6"/><rect x="1306" y="384" width="6" height="6"/>
    </g>
    <!-- handshake icon -->
    <g fill="none" stroke="#111" stroke-width="3.5" stroke-linejoin="round" stroke-linecap="round">
      <polygon points="1490,438 1504,416 1522,428 1508,450"/>
      <polygon points="1582,438 1568,416 1550,428 1564,450"/>
      <path d="M1522,430 L1540,424 L1552,428 L1538,438 L1530,434"/>
      <path d="M1508,450 L1530,470 Q1538,476 1544,468 L1564,450"/>
      <circle cx="1518" cy="458" r="4"/><circle cx="1526" cy="466" r="4"/><circle cx="1534" cy="472" r="4"/>
    </g>
    <!-- people icon -->
    <g fill="none" stroke="var(--red)" stroke-width="3">
      <circle cx="1780" cy="344" r="13"/>
      <path d="M1760,388 Q1760,362 1780,362 Q1800,362 1800,388 Z"/>
      <circle cx="1758" cy="358" r="9"/>
      <path d="M1742,388 Q1742,370 1756,370"/>
      <circle cx="1802" cy="358" r="9"/>
      <path d="M1818,388 Q1818,370 1804,370"/>
      <line x1="1742" y1="388" x2="1818" y2="388"/>
    </g>
    <!-- wifi icon -->
    <g fill="none" stroke="#111" stroke-width="5" stroke-linecap="round">
      <path d="M2006,464 Q2038,438 2070,464"/>
      <path d="M2016,474 Q2038,456 2060,474"/>
      <path d="M2026,484 Q2038,474 2050,484"/>
    </g>
    <circle cx="2038" cy="493" r="4.5" fill="#111"/>

    <!-- safety & quality -->
    <polygon points="1265,615 1615,615 1649,672 1615,730 1265,730 1230,672" fill="var(--red)"/>
    <rect x="1820" y="617" width="310" height="113" fill="var(--panel)"/>
    <polygon points="1742,604 1825,604 1862,672 1825,740 1742,740 1705,672" fill="#3f3f3f"/>
    <rect x="1340" y="797" width="306" height="135" fill="var(--panel)"/>
    <polygon points="1267,797 1345,797 1383,864 1345,932 1267,932 1229,864" fill="#767676"/>
    <rect x="1810" y="797" width="321" height="138" fill="var(--panel)"/>
    <polygon points="1735,797 1815,797 1853,866 1815,935 1735,935 1697,866" fill="#525252"/>

    <!-- indigenous inclusion -->
    <line x1="1679" y1="1018" x2="1679" y2="1382" stroke="#d6d6d6" stroke-width="2"/>
    <line x1="1238" y1="1188" x2="2120" y2="1188" stroke="#d6d6d6" stroke-width="2"/>
    <polygon points="1679,1078 1779,1135 1779,1250 1679,1307 1579,1250 1579,1135" fill="#fff"/>
    <g fill="none" stroke-width="14" stroke-linejoin="miter">
      <polyline points="1579,1192 1579,1135 1679,1078" stroke="var(--red)"/>
      <polyline points="1679,1078 1779,1135 1779,1192" stroke="#161616"/>
      <polyline points="1779,1192 1779,1250 1679,1307" stroke="var(--pink)"/>
      <polyline points="1679,1307 1579,1250 1579,1192" stroke="#444"/>
    </g>
  </svg>

  <!-- LEFT PAGE -->
  <h2 class="section-title red" style="top:193px">SITE REFURBISHMENT &amp; DEMOLITION</h2>
  <div class="row" style="top:246px"><div class="row-label label-red" style="width:385px">Comprehensive Refurbishment<br>And Demolition Services:</div><div class="row-text">For outdated telecom sites and structures.</div></div>
  <div class="row" style="top:329px"><div class="row-label label-red" style="width:305px">Environmentally<br>Responsible Dismantling:</div><div class="row-text">Focused on recycling materials and minimizing land impact.</div></div>

  <h2 class="section-title dark" style="top:469px">EMERGENCY RESPONSE SERVICES</h2>
  <div class="row" style="top:521px"><div class="row-label label-black" style="width:220px">24/7<br>Rapid Response:</div><div class="row-text">Over 450 callouts annually; 4,000+ emergencies resolved nationwide.</div></div>
  <div class="row" style="top:604px"><div class="row-label label-black" style="width:220px">Disaster Recovery:</div><div class="row-text">Comprehensive support during floods, bushfires for Velonet,<br>Marvaske, Trilumen, and regional clients.</div></div>

  <h2 class="section-title grey" style="top:754px">PROJECT EXPERIENCE</h2>
  <div class="row" style="top:806px"><div class="row-label g1" style="width:220px">Heritage Tower<br>Upgrade</div><div class="row-text">Enhanced safety and technology on culturally significant heritage<br>sites, preserving their integrity.</div></div>
  <div class="row" style="top:888px"><div class="row-label g2" style="width:220px">Wind Farm<br>Deployment</div><div class="row-text">Delivered power, fiber, and reinforced foundations for large-scale<br>renewable energy projects in high-wind environments.</div></div>
  <div class="row" style="top:968px"><div class="row-label g3" style="width:220px">Regional Fibre<br>Network</div><div class="row-text">Laid 200km of fiber in flood-prone regions, ensuring critical<br>infrastructure resilience.</div></div>
  <div class="row" style="top:1047px"><div class="row-label g4" style="width:261px">Indigenous Community<br>WiFi &amp; Connectivity</div><div class="row-text">Installed sustainable WiFi networks to bridge the digital divide,<br>supporting education, health, and business activities.</div></div>
  <div class="row" style="top:1132px"><div class="row-label g5" style="width:228px">Site Demolition<br>&amp; Refurbishment</div><div class="row-text">Safely decommissioned aging telecom sites and structures across<br>Australia, emphasizing land reuse and environmental care.</div></div>
  <div class="row" style="top:1213px;height:80px"><div class="row-label g6" style="width:280px">Access Track Construction<br>&amp; Remediation</div><div class="row-text">Developed new access roads and refurbished existing tracks to<br>facilitate project logistics, particularly in remote or<br>environmentally sensitive areas.</div></div>

  <div class="page-footer" style="left:166px"><span class="footer-brand">QUORVIN</span><span class="rule-dark"></span><span class="rule-light"></span><span class="page-num">4</span></div>

  <!-- RIGHT PAGE -->
  <div class="stats-title"><span class="light">KEY</span><span class="bold">STATS</span></div>
  <div class="stat-label" style="left:1161px;top:474px">+600 Sites<br>Supported</div>
  <div class="stat-label" style="left:1407px;top:284px">10-year Velonet<br>Partner</div>
  <div class="stat-label" style="left:1656px;top:474px">98% Client<br>Retention</div>
  <div class="stat-label" style="left:1907px;top:282px">Over 20 Indigenous<br>community WiFi<br>deployments</div>

  <div class="banner-text"><span class="thin">Commitment to</span><span class="strong">Safety &amp; Quality</span></div>

  <div class="hex-text" style="left:1710px;top:604px;width:148px;height:136px">“Pause<br>Twice, Work<br>Wise”<br>Protocol</div>
  <div class="panel-text" style="left:1886px;top:636px">Enforced pre-task risk<br>assessments to ensure<br>safety at every stage.</div>

  <div class="hex-text" style="left:1229px;top:797px;width:154px;height:135px">Certifications</div>
  <div class="panel-text" style="left:1398px;top:824px">ISO 45001 (Safety) |<br>ISO 9001 (Quality<br>Management).</div>

  <div class="hex-text" style="left:1697px;top:797px;width:156px;height:138px">Safety<br>Culture</div>
  <div class="panel-text" style="left:1860px;top:807px">Regular safety audits,<br>Indigenous-led training<br>programs, and safety<br>initiatives focused on<br>community well-being.</div>

  <div class="impact-head red" style="left:1238px;top:1035px">Elders Guidance Council:</div>
  <div class="impact-body" style="left:1238px;top:1069px">Provides guidance on community<br>engagement, cultural sensitivity,<br>and social responsibility.</div>
  <div class="impact-head" style="left:1789px;top:1035px">Supplier Diversity:</div>
  <div class="impact-body" style="left:1789px;top:1069px">30% procurement from<br>Indigenous-owned businesses,<br>fostering economic growth.</div>
  <div class="impact-head" style="left:1238px;top:1231px">Regional Employment:</div>
  <div class="impact-body" style="left:1238px;top:1265px">65% of our workforce originates<br>from local communities, creating<br>sustainable jobs.</div>
  <div class="impact-head red" style="left:1789px;top:1231px">Testimonial:</div>
  <div class="impact-body" style="left:1789px;top:1265px">“Quorvin’s partnership empowered<br>our community with jobs and<br>infrastructure that respects our<br>land.” – Local Indigenous Leader</div>
  <div class="impact-core">INDIGENOUS INCLUSION &amp; COMMUNITY IMPACT</div>

  <div class="page-footer" style="left:1226px;width:905px"><span class="footer-brand">QUORVIN</span><span class="rule-dark"></span><span class="rule-light"></span><span class="page-num">5</span></div>
</div>
</body>
</html>
```